Smart Design for Global Industrial Business

We are commissioned to replace an existing industrial business website with a new website with new branding and layout for CMS / Responsive (Wordpress). The existing website is to be replaced (rvtbindings.com) with one that is more in keeping with the new brand book and modern design standards.
Note that they have two online stores (rvt-gripping.co.uk and .com) and this site will need to fit with those, whilst being very different and much more about RVT and their scope / reach.
Please just design the homepage first as we will try to give everyone a chance to build from there if they are heading in the right direction.
The eventual delivery will be of all the wireframes, in source file format (ideally PSD) as well as PNGs.
We will aim to feedback in detail to all participants, but if you really don't try that hard, it may be brief!

Target Market(s)

Buyers in companies who are looking for clamping / restraining products - to persuade them that these are the best, most reliable, products.

Industry/Entity Type

Industrial safety/banding products

Number of Pages Required

5+ page

Font styles to use
Sans Serif
Other font styles liked:
• see current websites

Requirements
Must have
• A really good consistent level of design with consideration of mobile users and lead generation.
Nice to have
• I just want to see good creative, if possible. Don't try too many things, keep it simple.
Should not have
• No untidiness or lack of consistency.

```html
<!DOCTYPE html>
<html lang="en">
<head>
<meta charset="utf-8">
<title>RVT Fasteners – Clamping and Banding Solutions</title>
<link rel="stylesheet" href="https://fonts.googleapis.com/css2?family=Lato:wght@400;700;900&display=swap">
<style>
:root{
  --orange:#e8401c;
  --navy:#17263a;
  --ink:#2f3338;
  --muted:#555a60;
  --grey:#ececec;
  --white:#ffffff;
}
*{box-sizing:border-box;margin:0;padding:0}
html,body{width:1200px;height:4743px;overflow:hidden}
body{font-family:'Lato',Arial,sans-serif;color:var(--ink);background:var(--white)}
a{color:inherit;text-decoration:none}
.btn{display:inline-flex;align-items:center;justify-content:center;background:var(--orange);color:var(--white);font-weight:700;font-size:16px;text-transform:uppercase;letter-spacing:.2px}

/* header */
.site-header{position:relative;height:142px;border-top:7px solid var(--orange);background:var(--white)}
.utility-nav{position:absolute;right:59px;top:0;width:341px;height:48px;background:var(--orange);color:var(--white);font-size:14px;font-weight:700;display:flex;align-items:center;justify-content:center;gap:14px;clip-path:polygon(12px 0,100% 0,100% 100%,0 100%)}
.brand{position:absolute;left:74px;top:34px;display:flex;align-items:center;gap:12px;font-size:56px;font-weight:900;color:var(--navy);letter-spacing:1px}
.brand-dot{width:22px;height:22px;background:var(--orange);border-radius:50%}
.main-nav{position:absolute;right:73px;top:94px;display:flex;gap:40px;font-size:14px;font-weight:700;color:var(--navy)}

/* hero */
.hero{position:relative;height:662px;background:radial-gradient(circle at 50% 50%,#6e6a66 0%,#4d4a47 55%,#2e2c2a 100%);text-align:center;color:var(--white)}
.hero h1{position:absolute;top:375px;left:0;right:0;font-size:40px;font-weight:900;line-height:51px;text-transform:uppercase}
.hero-actions{position:absolute;top:502px;left:0;right:0;display:flex;justify-content:center;gap:18px}
.hero-actions .btn{width:218px;height:58px}

/* intro */
.intro{height:401px;padding:63px 83px 0;text-align:center;font-size:17px;line-height:32px;color:var(--muted)}
.intro p+p{margin-top:10px}

/* feature bands */
.feature{position:relative;overflow:hidden}
.feature-weather{height:658px;background:linear-gradient(160deg,#6b7a82 0%,#3fbf4a 30%,#2fa33c 50%,#8e7ca6 75%,#b6a8c6 100%)}
.feature-custom{height:655px;background:linear-gradient(120deg,#cfcccb 0%,#8d8a89 30%,#8f2e2a 55%,#d6d2d0 80%,#e4e1df 100%)}
.feature-panel{position:absolute;bottom:0;background:rgba(255,255,255,.88);padding:34px 74px 0}
.feature-weather .feature-panel{left:0;width:587px;height:437px}
.feature-custom .feature-panel{left:613px;width:587px;height:434px;padding-left:23px}
.feature-panel h2{font-size:27px;font-weight:900;line-height:37px;color:var(--navy);text-transform:uppercase}
.feature-panel p{font-size:15px;line-height:27px;color:var(--ink);margin-top:14px}
.select{margin-top:22px;width:315px;height:46px;border:1px solid #bbb;background:var(--white);display:flex;align-items:center;justify-content:space-between;padding:0 18px;font-size:15px;color:#555}
.feature-custom .btn{margin-top:26px;width:240px;height:46px}

.spacer{height:81px}

/* case studies */
.case-studies{height:504px;background:var(--navy);padding-top:76px}
.section-title{text-align:center;font-size:27px;font-weight:900;text-transform:uppercase}
.case-studies .section-title{color:var(--white)}
.card-row{display:flex;gap:28px;padding:0 74px;margin-top:36px}
.case-card{width:242px;height:274px;background:var(--white);display:flex;flex-direction:column;align-items:center;padding-top:14px}
.case-card .thumb{width:170px;height:170px;border-radius:6px;background:radial-gradient(circle,#d9d9d9 0%,#8a8a8a 70%,#fff 71%)}
.case-card h3{margin-top:auto;margin-bottom:30px;font-size:17px;font-weight:700;text-align:center;line-height:26px;color:var(--navy)}

/* news */
.news{height:455px;padding-top:48px}
.news .section-title{color:var(--navy)}
.news-item{width:242px}
.news-item .thumb{height:197px}
.news-item p{margin-top:20px;font-size:15px;font-weight:700;line-height:26px;color:var(--navy)}
.news .card-row{margin-top:36px}

/* offices */
.offices{height:712px;background:var(--grey);padding:59px 73px 0;display:flex;gap:32px}
.office{width:511px;text-align:center}
.office .map{height:266px;border:3px solid #d6d6d6;background:linear-gradient(135deg,#f3f3f1,#e2e3e0)}
.office h2{margin-top:38px;font-size:27px;font-weight:700;line-height:37px;color:var(--ink)}
.office h3{margin-top:6px;font-size:19px;font-weight:700;color:var(--ink)}
.office address{font-style:normal;font-size:16px;line-height:30px;margin-top:6px}
.office .tel{font-weight:700;margin-top:4px;font-size:16px}
.office .btn{margin-top:22px;width:238px;height:46px}

/* footer */
.site-footer{height:473px;background:var(--navy);color:var(--white);position:relative;padding:52px 74px 0}
.footer-cols{display:flex}
.footer-col:nth-child(1){width:257px}
.footer-col:nth-child(2){width:293px}
.footer-col:nth-child(3){width:259px}
.footer-col h4{font-size:22px;font-weight:700;margin-bottom:14px}
.footer-col li{list-style:none;font-size:14px;line-height:37px}
.footer-col li::before{content:"»";color:var(--orange);font-weight:900;margin-right:16px}
.contact-block{font-size:14px;line-height:27px}
.contact-block strong{display:block;margin-top:4px}
.contact-block .gap{margin-top:12px}
.social{display:flex;gap:24px;margin-top:32px;padding-left:0}
.social span{width:18px;height:18px;border-radius:50%;background:var(--orange)}
.footer-bottom{position:absolute;left:74px;right:74px;bottom:26px;display:flex;justify-content:space-between;font-size:13px}
</style>
</head>
<body>

<header class="site-header">
  <nav class="utility-nav"><a>ABOUT US</a><span>/</span><a>NEWS</a><span>/</span><a>CONTACT US</a></nav>
  <a class="brand"><span class="brand-dot"></span>RVT</a>
  <nav class="main-nav"><a>HOSE CLAMPS</a><a>BANDING &amp; SADDLES</a><a>CUSTOM SOLUTIONS</a><a>APPLICATIONS</a><a>CASE STUDIES</a></nav>
</header>

<section class="hero" role="img" aria-label="Pile of stainless steel worm-drive hose clamps">
  <h1>The leading manufacturer and supplier of<br>clamping and banding solutions</h1>
  <div class="hero-actions"><a class="btn">Hose Clamps</a><a class="btn">Banding &amp; Saddles</a><a class="btn">Custom Solutions</a></div>
</section>

<section class="intro">
  <p>Sed ut perspiciatis unde omnis iste natus error sit voluptatem accusantium doloremque laudantium, totam rem aperiam, eaque ipsa quae ab illo inventore veritatis et quasi architecto beatae vitae dicta sunt explicabo. Nemo enim ipsam voluptatem quia voluptas sit aspernatur aut odit aut fugit, sed quia consequuntur magni dolores eos qui ratione voluptatem sequi nesciunt. Neque porro quisquam est, qui dolorem ipsum quia dolor sit amet, consectetur, adipisci velit, sed quia non numquam eius modi tempora incidunt ut labore et dolore magnam.</p>
  <p>Sed ut perspiciatis unde omnis iste natus error sit voluptatem accusantium doloremque laudantium, totam rem aperiam, eaque ipsa quae ab illo inventore veritatis et quasi architecto beatae vitae dicta sunt explicabo. Nemo enim ipsam voluptatem quia voluptas sit aspernatur aut odit aut fugit, sed quia consequuntur</p>
</section>

<section class="feature feature-weather" role="img" aria-label="Green and purple pipes held by banding saddles">
  <div class="feature-panel">
    <h2>Water sun. Cold. Salt. Wind...<br>We've got it covered</h2>
    <p>Sed ut perspiciatis unde omnis iste natus error sit voluptatem accusantium doloremque laudantium, totam rem aperiam, eaque ipsa quae ab illo inventore veritatis et quasi architecto beatae vitae dicta sunt explicabo.</p>
    <p>Nemo enim ipsam&nbsp; voluptatem quia voluptas sit aspernatur aut odit aut fugit, sed quia consequuntur iure reprehenderit qui in ea voluptate velit esse quam.</p>
    <div class="select"><span>Choose a Challange</span>
      <svg width="10" height="16" viewBox="0 0 10 16"><path d="M5 1 9 6H1zM5 15 1 10h8z" fill="#333"/></svg></div>
  </div>
</section>

<section class="feature feature-custom" role="img" aria-label="Red pipe suspended in a clevis hanger clamp">
  <div class="feature-panel">
    <h2>Custom Solutions</h2>
    <p>Sed ut perspiciatis unde omnis iste natus error sit voluptatem accusantium doloremque laudantium, totam rem aperiam, eaque ipsa quae ab illo inventore veritatis et quasi architecto beatae vitae dicta sunt explicabo.</p>
    <a class="btn">Find out more</a>
    <p>Nemo enim ipsam&nbsp; voluptatem quia voluptas sit aspernatur aut odit aut fugit, sed quia consequuntur iure reprehenderit qui in ea voluptate velit esse quam.</p>
  </div>
</section>

<div class="spacer"></div>

<section class="case-studies">
  <h2 class="section-title">Case Studies- RVT Products in Place</h2>
  <div class="card-row">
    <article class="case-card"><div class="thumb" role="img" aria-label="Hose clamp product"></div><h3>ICCP - Grey Harbour</h3></article>
    <article class="case-card"><div class="thumb" role="img" aria-label="Black band clamp product"></div><h3>Downhole - Andoria Energy</h3></article>
    <article class="case-card"><div class="thumb" role="img" aria-label="Cable management band"></div><h3>Offshore<br>Cable Management</h3></article>
    <article class="case-card"><div class="thumb" role="img" aria-label="Moulded seeder parts"></div><h3>Seeders - Feldmark</h3></article>
  </div>
</section>

<section class="news">
  <h2 class="section-title">News, Events Features</h2>
  <div class="card-row">
    <article class="news-item"><div class="thumb" role="img" aria-label="Offshore worker at a rig" style="background:linear-gradient(160deg,#b8c7d6,#7a3030 55%,#2e3b4e)"></div><p>Nemo enim ipsam voluptatem quia voluptas sit..</p></article>
    <article class="news-item"><div class="thumb" role="img" aria-label="Pipeline laid along a cleared track" style="background:linear-gradient(180deg,#c9d3dd,#7d8a77 45%,#c0873c 80%,#6a5a44)"></div><p>Nemo enim ipsam voluptatem quia voluptas sit..</p></article>
    <article class="news-item"><div class="thumb" role="img" aria-label="Digital caliper measuring a hose fitting" style="background:linear-gradient(160deg,#e6ece8,#8fa39a 50%,#4fa0d8)"></div><p>Nemo enim ipsam voluptatem quia voluptas sit..</p></article>
    <article class="news-item"><div class="thumb" role="img" aria-label="Testing machinery in a workshop" style="background:linear-gradient(160deg,#3a3a3a,#8b8478 50%,#2a2a2a)"></div><p>Nemo enim ipsam voluptatem quia voluptas sit..</p></article>
  </div>
</section>

<section class="offices">
  <div class="office">
    <div class="map" role="img" aria-label="Map of the UK office location"></div>
    <h2>RVT FASTENERS LIMITED for UK,<br>EU, EMEA &amp; Worldwide</h2>
    <h3>Main Office:</h3>
    <address>Binding House 2nd Avenue<br>Northgate Industrial Estate Kelmore, Avonbury,<br>Wessex KB4 7QT United Kingdom</address>
    <p class="tel">Tel: +44 (0)1632 960418</p>
    <a class="btn">Contact Us</a>
  </div>
  <div class="office">
    <div class="map" role="img" aria-label="Map of the USA office location"></div>
    <h2>RVT FASTENERS CORP for<br>USA &amp; Canada</h2>
    <h3>Main Office:</h3>
    <address>Larkfield 1840 Business Centre<br>18410 Larkfield Road,<br>Suite 12 Brayton, Texas, 77001 USA</address>
    <p class="tel">Tel: 1-800 555 0142</p>
    <a class="btn">Contact Us</a>
  </div>
</section>

<footer class="site-footer">
  <div class="footer-cols">
    <div class="footer-col"><h4>Hose Clamps</h4><ul><li>Bolt Clips</li><li>Swiftclamp</li><li>Swiftclik</li><li>Air Tools</li><li>Distributed Brands</li></ul></div>
    <div class="footer-col"><h4>Banding &amp; Saddles</h4><ul><li>Prime Band</li><li>Prime Tie</li><li>Prime Protectors</li><li>Prime Saddles</li><li>Installation Tools</li></ul></div>
    <div class="footer-col"><h4>Discover RVT</h4><ul><li>Custom Solutions</li><li>Applications</li><li>Case Studies</li><li>Quality &amp; Testing</li><li>Facility</li><li>Contact Us</li></ul></div>
    <div class="footer-col"><h4>Contact RVT</h4>
      <div class="contact-block">
        <p>Send an Email</p>
        <strong>UK/EU</strong>
        <p>Tel: +44 (0)1632 960418</p>
        <p>Online Store</p>
        <strong class="gap">US/CA</strong>
        <p>Tel: 555 201 7734</p>
        <p>Toll free: 1-800 555 0142</p>
        <p>Online Store</p>
      </div>
      <div class="social"><span></span><span></span><span></span></div>
    </div>
  </div>
  <div class="footer-bottom"><span>Copyright © 2021. Company Name.&nbsp; All Right Reserved</span><span>Sitemap Terms of Use &nbsp; / &nbsp; Privacy Policy &nbsp; / &nbsp; Contact Us</span></div>
</footer>

</body>
</html>
```